Web Developer Needs a Business Card Design

I need a personal business card design that represents me as a web developer for potential employers. I would like the background to be a dark color on the front for contrast with my logo and name. The back will have all my information along with a smaller version of the logo. I want something with a modern look and feel, not too conservative. This will be used for potential employers and freelance work.

Industry/Entity Type

Business

Contact Information for Business Card

Front should have my logo and name. The back should have all my personal information which would include: name: Tom Varulek, phone: 570-614-3098, email: tomvarulek@quillbox.net, website url: www.tomvarulek.net, logo, web developer.

Font styles to use
Sans Serif

Requirements
Must have
• Must include my logo. The color palette base color will be the logo color.

```html
<!DOCTYPE html>
<html lang="en">
<head>
<meta charset="utf-8">
<title>Tom Varulek – Business Card</title>
<link rel="stylesheet" href="https://fonts.googleapis.com/css2?family=Questrial&display=swap">
<style>
  :root {
    --backdrop: #8a8a8a;
    --teal: #4cc8a8;
    --teal-soft: #47bea0;
    --paper: #ececec;
    --ink: #151515;
    --text: #585858;
    --rule: #4a4a4a;
  }
  * { margin: 0; padding: 0; box-sizing: border-box; }
  html, body {
    width: 1200px;
    height: 900px;
    overflow: hidden;
    background: var(--backdrop);
    font-family: "Questrial", sans-serif;
  }
  .stage { position: relative; width: 1200px; height: 900px; }

  .card {
    position: absolute;
    left: 321px;
    width: 507px;
    height: 290px;
    overflow: hidden;
  }

  /* Front */
  .card-front { top: 119px; background: var(--teal); }
  .front-field {
    position: absolute; inset: 0;
    background: linear-gradient(180deg, var(--teal) 0%, var(--teal-soft) 100%);
  }
  .front-mark {
    position: absolute;
    left: 214px; top: 116px;
    width: 78px; height: 78px;
    border: 4px solid var(--ink);
    border-radius: 50%;
    display: flex; align-items: center; justify-content: center;
    color: var(--ink);
    font-size: 11px;
    white-space: nowrap;
  }

  /* Back */
  .card-back { top: 470px; background: var(--paper); }
  .back-mark {
    position: absolute;
    left: 355px; top: 27px;
    width: 118px; height: 118px;
    border: 4px solid var(--teal);
    border-radius: 50%;
    display: flex; align-items: center; justify-content: center;
    color: var(--teal);
    font-size: 16px;
    white-space: nowrap;
  }
  .holder-name {
    position: absolute;
    left: 28px; top: 140px;
    font-size: 24px;
    color: var(--teal);
    letter-spacing: 0.3px;
  }
  .holder-role {
    position: absolute;
    left: 28px; top: 168px;
    font-size: 15px;
    color: var(--text);
  }
  .role-rule {
    position: absolute;
    left: 187px; top: 177px;
    width: 290px; height: 2px;
    background: var(--rule);
  }
  .contact-list {
    position: absolute;
    list-style: none;
    font-size: 13.5px;
    color: var(--text);
  }
  .contact-list li {
    display: flex; align-items: center;
    height: 22.5px;
  }
  .contact-list svg, .contact-dot { flex: none; margin-right: 8px; }
  .contact-main { left: 28px; top: 195px; }
  .contact-web { left: 332px; top: 192px; }
  .contact-dot {
    width: 13px; height: 13px;
    border-radius: 50%;
    background: var(--teal);
  }
  .back-band {
    position: absolute;
    left: 0; bottom: 0;
    width: 100%; height: 13px;
    background: var(--teal);
  }
</style>
</head>
<body>
<main class="stage">

  <section class="card card-front">
    <div class="front-field" role="img" aria-label="Repeating pattern of the personal monogram in soft teal tones"></div>
    <div class="front-mark">Tom Varulek</div>
  </section>

  <section class="card card-back">
    <div class="back-mark">Tom Varulek</div>

    <h1 class="holder-name">Tom Varulek</h1>
    <p class="holder-role">Front-End Developer</p>
    <div class="role-rule"></div>

    <ul class="contact-list contact-main">
      <li>
        <svg width="13" height="13" viewBox="0 0 24 24" aria-hidden="true"><path fill="#4cc8a8" d="M6.6 10.8a15 15 0 0 0 6.6 6.6l2.2-2.2a1 1 0 0 1 1-.25 11.4 11.4 0 0 0 3.6.57 1 1 0 0 1 1 1V20a1 1 0 0 1-1 1A17 17 0 0 1 3 4a1 1 0 0 1 1-1h3.5a1 1 0 0 1 1 1c0 1.25.2 2.45.57 3.57a1 1 0 0 1-.25 1z"/></svg>
        570-614-3098
      </li>
      <li>
        <svg width="13" height="13" viewBox="0 0 24 24" aria-hidden="true"><rect x="2" y="5" width="20" height="14" fill="#4cc8a8"/><path d="M2 5l10 8 10-8" fill="none" stroke="#ececec" stroke-width="2"/></svg>
        tomvarulek@quillbox.net
      </li>
      <li>
        <svg width="13" height="13" viewBox="0 0 24 24" aria-hidden="true"><circle cx="12" cy="12" r="10" fill="#4cc8a8"/><path d="M2 12h20M12 2c3 3 3 17 0 20M12 2c-3 3-3 17 0 20" fill="none" stroke="#ececec" stroke-width="1.5"/></svg>
        www.tomvarulek.net
      </li>
    </ul>

    <ul class="contact-list contact-web">
      <li><span class="contact-dot"></span>@tomvarulek.net</li>
      <li><span class="contact-dot"></span>tomvarulek.net</li>
      <li><span class="contact-dot"></span>tomvarulek.net</li>
    </ul>

    <div class="back-band"></div>
  </section>

</main>
</body>
</html>
```